Harbourline Electrical Solutions

On one side. LOGO (underneath:) Commercial Industrial Residential

- NAME & CONTACT DETAILS

Marcus T. Hollings
Project Manager

(Cell icon) (441) 555-0187
(Email icon) hlelectricalsolutions@mailvento.com
(Facebook & Instagram icons )@hlelectricalsolutions

Other side: LOGO - underneath ELECTRICAL CONSTRUCTION & MAINTENANCE . LED LIGHTING & AUTOMATION . LIFE SAFETY SYSTEMS (FIRE ALARM / SECURITY) . DATA & COMMUNICATION

```html
<!DOCTYPE html>
<html lang="en">
<head>
<meta charset="utf-8">
<title>Harbourline Electrical Solutions – Business Card</title>
<link rel="stylesheet" href="https://fonts.googleapis.com/css2?family=Montserrat:wght@400;500;600;700&display=swap">
<style>
  :root {
    --backdrop: #2a2a2b;
    --teal: #17586e;
    --ink: #111112;
    --white: #ffffff;
    --rule-grey: #4a4a4a;
  }
  * { box-sizing: border-box; margin: 0; padding: 0; }
  html, body { width: 1200px; height: 1000px; overflow: hidden; }
  body {
    background: var(--backdrop);
    font-family: "Montserrat", sans-serif;
    position: relative;
  }
  .card {
    position: absolute;
    left: 250px;
    width: 700px;
    height: 400px;
    border-radius: 22px;
    overflow: hidden;
  }

  /* Front */
  .card--front { top: 70px; background: var(--white); }
  .front__brand {
    position: absolute;
    top: 0; left: 0; right: 0;
    height: 238px;
    display: flex;
    align-items: center;
    justify-content: center;
  }
  .wordmark {
    color: var(--teal);
    font-weight: 600;
    text-transform: uppercase;
    letter-spacing: 0.22em;
    line-height: 1.12;
    font-size: 30px;
  }
  .wordmark span { display: block; }
  .front__band {
    position: absolute;
    left: 0; right: 0; bottom: 0;
    height: 162px;
    background: var(--teal);
    border-top: 5px solid var(--rule-grey);
    display: grid;
    grid-template-columns: 1.35fr 1fr;
    gap: 10px 24px;
    align-content: center;
    padding: 0 44px;
  }
  .service {
    color: var(--white);
    font-size: 13px;
    font-weight: 500;
    letter-spacing: 0.06em;
    text-transform: uppercase;
    display: flex;
    align-items: center;
    gap: 8px;
    white-space: nowrap;
  }
  .service::before {
    content: "";
    width: 7px; height: 7px;
    border: 1.5px solid var(--white);
    border-radius: 50%;
    flex: none;
  }

  /* Back */
  .card--back { top: 530px; background: var(--ink); }
  .back__brand {
    position: absolute;
    top: 46px; left: 0; right: 0;
    display: flex;
    justify-content: center;
  }
  .back__brand .wordmark { color: var(--white); font-size: 26px; }
  .identity {
    position: absolute;
    top: 200px; left: 60px;
    width: 280px;
    text-align: right;
    padding-right: 22px;
    border-right: 2px solid var(--teal);
  }
  .identity__name {
    color: var(--teal);
    font-size: 27px;
    font-weight: 700;
    letter-spacing: 0.02em;
  }
  .identity__title {
    color: var(--white);
    font-size: 16px;
    margin-top: 4px;
  }
  .contact {
    position: absolute;
    top: 202px; left: 362px;
    list-style: none;
    display: flex;
    flex-direction: column;
    gap: 12px;
  }
  .contact li {
    color: var(--white);
    font-size: 15px;
    display: flex;
    align-items: center;
    gap: 10px;
  }
  .contact .icon {
    width: 24px; height: 24px;
    border-radius: 50%;
    background: var(--teal);
    display: grid;
    place-items: center;
    flex: none;
  }
  .back__stripe {
    position: absolute;
    left: 0; right: 0;
    bottom: 36px;
    height: 50px;
    background: var(--teal);
    display: flex;
    align-items: center;
    justify-content: center;
    gap: 10px;
    color: var(--white);
    font-size: 16px;
    font-weight: 500;
  }
  .social-mark {
    width: 12px; height: 12px;
    background: var(--white);
    border-radius: 2px;
  }
</style>
</head>
<body>

  <section class="card card--front" aria-label="Card front">
    <div class="front__brand">
      <div class="wordmark"><span>Harbourline</span><span>Electrical</span><span>Solutions</span></div>
    </div>
    <ul class="front__band">
      <li class="service">Electrical Construction &amp; Maintenance</li>
      <li class="service">LED Lighting &amp; Automation</li>
      <li class="service">Life Safety Systems (Fire Alarm / Security)</li>
      <li class="service">Data &amp; Communication</li>
    </ul>
  </section>

  <section class="card card--back" aria-label="Card back">
    <div class="back__brand">
      <div class="wordmark"><span>Harbourline</span><span>Electrical</span><span>Solutions</span></div>
    </div>

    <div class="identity">
      <p class="identity__name">Marcus T. Hollings</p>
      <p class="identity__title">Project Manager</p>
    </div>

    <ul class="contact">
      <li>
        <span class="icon">
          <svg width="13" height="13" viewBox="0 0 24 24" aria-hidden="true"><path fill="#fff" d="M6.6 10.8a15.1 15.1 0 0 0 6.6 6.6l2.2-2.2a1 1 0 0 1 1-.25 11.4 11.4 0 0 0 3.6.57 1 1 0 0 1 1 1V20a1 1 0 0 1-1 1A17 17 0 0 1 3 4a1 1 0 0 1 1-1h3.5a1 1 0 0 1 1 1c0 1.25.2 2.45.57 3.6a1 1 0 0 1-.25 1z"/></svg>
        </span>
        (441) 555-0187
      </li>
      <li>
        <span class="icon">
          <svg width="13" height="13" viewBox="0 0 24 24" aria-hidden="true"><rect x="2" y="5" width="20" height="14" rx="2" fill="#fff"/><path d="M3 6l9 7 9-7" fill="none" stroke="#17586e" stroke-width="2"/></svg>
        </span>
        hlelectricalsolutions@mailvento.com
      </li>
    </ul>

    <div class="back__stripe">
      <span class="social-mark" aria-hidden="true"></span>
      @hlelectricalsolutions
    </div>
  </section>

</body>
</html>
```